Business card design for Automotive workshop

We need a business card for a new automotive repair and tyre shop called Keelstone Prime Automotive located in New Zealand. We are a clean, modern and fresh workshop and company.

Front needs to feature logo,
my name:
Marlo Fenwicke (director)

Address:
48 Tarn Lane
Whitianga 3510

Phone: 07 594 2713
Mobile: 027 451 9362
Email: office@keelstoneautomotive.example.nz
Website: keelstoneautomotive.example.nz

Back needs to feature an area to write down appointment details, date and time.

Also feature a list of jobs and work we do such as,
Vehicle Servicing
All Mechanical Repairs
Warrant of Fitness
Tyres & Wheel Alignments
Automotive Diagnostics
Automotive Parts & Supplies

```html
<!DOCTYPE html>
<html lang="en">
<head>
<meta charset="utf-8">
<title>Keelstone Prime Automotive – Business Cards</title>
<link rel="stylesheet" href="https://fonts.googleapis.com/css2?family=Roboto:wght@400;500;700&display=swap">
<style>
  :root {
    --bg: #5a5a5c;
    --card-dark: #262627;
    --card-black: #050505;
    --white: #ffffff;
    --red: #e21b23;
    --ink: #111111;
    --muted: #e8e8e8;
  }
  * { box-sizing: border-box; margin: 0; padding: 0; }
  html, body { width: 1200px; height: 960px; overflow: hidden; }
  body {
    background: var(--bg);
    font-family: "Roboto", Arial, sans-serif;
    position: relative;
  }
  .card {
    position: absolute;
    width: 580px;
    height: 332px;
    overflow: hidden;
    box-shadow: 0 18px 40px rgba(0,0,0,.45);
  }

  /* Back card: services + appointment */
  .card-back {
    left: 70px; top: 90px;
    background: var(--card-dark);
    color: var(--white);
  }
  .card-back .brand {
    position: absolute; top: 34px; left: 0; right: 0;
    text-align: center;
    font-size: 30px; font-weight: 700; letter-spacing: 1px;
    text-transform: uppercase;
    color: var(--white);
  }
  .card-back .headline {
    position: absolute; top: 92px; left: 0; right: 0;
    text-align: center;
    color: var(--red);
    font-size: 15px; font-weight: 500; letter-spacing: .5px;
  }
  .services {
    position: absolute; top: 114px; left: 0; right: 0;
    text-align: center;
    font-size: 13px; line-height: 19px;
    color: var(--muted);
  }
  .services .dot { color: var(--red); margin: 0 6px; }
  .appointment {
    position: absolute; left: 22px; right: 22px; bottom: 22px;
    height: 112px;
    background: var(--white);
    padding: 22px 20px 0;
  }
  .appointment-row {
    display: flex; align-items: flex-end; gap: 6px;
    height: 34px;
    font-size: 14px; font-weight: 500;
    color: var(--red);
  }
  .appointment-row .fill {
    flex: 1;
    border-bottom: 1.5px dotted #666;
    margin-bottom: 4px;
  }
  .appointment-row .label-time { margin-left: 8px; }
  .appointment-row .fill.short { flex: 0.85; }

  /* Front card: contact details */
  .card-front {
    left: 550px; top: 530px;
    background: var(--white);
  }
  .card-front .divider { position: absolute; inset: 0; }
  .card-front .brand {
    position: absolute; left: 28px; top: 150px; width: 250px;
    text-align: center;
    font-size: 19px; font-weight: 700; letter-spacing: .5px;
    text-transform: uppercase;
    color: var(--ink);
    line-height: 1.25;
  }
  .contact {
    position: absolute; left: 345px; top: 40px; right: 20px;
    color: var(--white);
  }
  .contact .name {
    color: var(--red);
    font-size: 21px; font-weight: 700;
  }
  .contact .role {
    font-size: 13px; font-weight: 500;
    margin-top: 2px;
  }
  .contact .address {
    font-size: 12.5px; line-height: 17px;
    margin-top: 34px;
  }
  .contact .lines {
    font-size: 12.5px; line-height: 17px;
    margin-top: 20px;
    white-space: nowrap;
  }
  .contact .small { font-size: 11px; }
</style>
</head>
<body>

<section class="card card-back" aria-label="Business card back">
  <div class="brand">Keelstone Prime Automotive</div>
  <div class="headline">VEHICLE SERVICING</div>
  <div class="services">
    All Mechanical Repairs<span class="dot">•</span>Warrant of Fitness<span class="dot">•</span>Tyres &amp; Wheel Alignments<br>
    Automotive Diagnostics<span class="dot">•</span>Automotive Parts &amp; Supplies
  </div>
  <div class="appointment">
    <div class="appointment-row">
      <span>Date:</span><span class="fill"></span>
      <span class="label-time">Time:</span><span class="fill short"></span>
    </div>
    <div class="appointment-row">
      <span>Date:</span><span class="fill"></span>
      <span class="label-time">Time:</span><span class="fill short"></span>
    </div>
  </div>
</section>

<section class="card card-front" aria-label="Business card front">
  <svg class="divider" width="580" height="332" viewBox="0 0 580 332" aria-hidden="true">
    <path d="M276 0 L312 48 L312 84 L356 332 L580 332 L580 0 Z" fill="var(--card-black)"/>
    <path d="M276 0 L312 48 L312 84 L356 332" fill="none" stroke="var(--red)" stroke-width="3"/>
  </svg>
  <div class="brand">Keelstone Prime<br>Automotive</div>
  <div class="contact">
    <div class="name">Marlo Fenwicke</div>
    <div class="role">Director</div>
    <div class="address">48 Tarn Lane<br>Whitianga 3510</div>
    <div class="lines">
      P. 07 594 2713<br>
      C. 027 451 9362<br>
      <span class="small">office@keelstoneautomotive.example.nz</span><br>
      <span class="small">www.keelstoneautomotive.example.nz</span>
    </div>
  </div>
</section>

</body>
</html>
```